Lifecoach needs website design based on a standard Wordpress theme

I need a website for my new lifecoaching business that can be easily implemented in Wordpress, it needs to be compatible with a standard Wordpress theme. So I can place the pictures, texts etc. in a standard theme of Wordpress.

I want the design to be a very good feeling and playfull one, based on my logo.

Target Market(s)

I will coach people to reach their goals and dreams in life.

Industry/Entity Type

Business

Requirements
Must have
• Can be easy implemented in Wordpress.
Nice to have
• Photo's of nature are nice.

```html
<!DOCTYPE html>
<html lang="en">
<head>
<meta charset="utf-8">
<title>Mara Lindqvist Lifecoach</title>
<link rel="stylesheet" href="https://fonts.googleapis.com/css2?family=Lato:wght@300;400;700&display=swap">
<style>
:root{
  --navy:#0b4f7e;
  --navy-dark:#063f66;
  --sky:#1bb6ec;
  --link:#1a9ad6;
  --heading:#0e4a75;
  --text:#444;
  --muted:#9aa3ab;
  --page:#eef3f6;
}
*{margin:0;padding:0;box-sizing:border-box}
html,body{width:1024px;height:1200px;overflow:hidden}
body{font-family:'Lato',sans-serif;background:var(--page);position:relative;color:var(--text)}
.abs{position:absolute}
.topbar{left:0;top:0;width:1024px;height:32px;background:var(--navy)}
.topbar .info{top:10px;font-size:9.5px;color:#fff;display:flex;align-items:center;gap:6px;white-space:nowrap}
.header{left:0;top:32px;width:1024px;height:72px;background:#fff}
.brand-box{left:120px;top:0;width:270px;height:94px;background:linear-gradient(#fff,#e4e4e4);border:1px solid #ccc;border-top:none;box-shadow:0 2px 3px rgba(0,0,0,.25);display:flex;align-items:center;gap:10px;padding-left:12px}
.brand-mark{width:62px;height:62px;border-radius:50%;border:3px solid var(--link);flex:none}
.brand-name{font-size:20px;color:var(--heading);line-height:1.05;font-weight:400}
.brand-name small{display:block;font-size:12px;letter-spacing:1px;text-align:center}
.nav a{position:absolute;top:60px;font-size:12px;color:#555;text-decoration:none}
.nav a.active{color:var(--link)}
.hero{left:0;top:104px;width:1024px;height:384px;background:linear-gradient(180deg,#7fb2cc 0%,#c8d8cf 35%,#f3d38a 60%,#e88a1e 78%,#2a1406 90%,#120a04 100%)}
.hero-quote{right:120px;top:238px;text-align:right;font-size:24px;font-weight:300;color:var(--heading);line-height:29px;white-space:nowrap}
.dots{left:847px;top:464px;display:flex;gap:8px}
.dots i{width:8px;height:8px;border-radius:50%;background:#fff;display:block}
.dots i.on{background:var(--link);box-shadow:0 0 0 2px #fff}
.welcome{left:0;top:511px;width:1024px;text-align:center;font-size:24px;font-weight:300;color:#333}
.welcome b{color:var(--sky);font-weight:700}
.card-img{top:568px;width:245px;height:144px}
.card-title{top:724px;font-size:15px;color:var(--heading)}
.card-text{top:746px;width:240px;font-size:10px;line-height:16px;color:var(--muted)}
.news-head{left:662px;top:564px;font-size:14px;font-weight:700;color:var(--heading);display:flex;align-items:center;gap:7px}
.news-rule{left:662px;top:598px;width:239px;border-top:3px dotted #ccd3d8}
.news-title{left:662px;font-size:12px;color:#222}
.news-thumb{left:660px;width:68px;height:58px;background:linear-gradient(135deg,#d8dde2,#5d6670)}
.news-text{left:742px;width:162px;font-size:9px;line-height:14.5px;color:#666}
.news-date{left:742px;font-size:7.5px;color:#555}
.band{left:0;top:822px;width:1024px;height:174px;background:linear-gradient(180deg,#9ec3d6 0%,#e6e1c6 55%,#f5d79b 100%)}
.band-title{left:0;top:845px;width:1024px;text-align:center;font-size:20px;font-weight:300;color:#333}
.avatar{top:890px;width:40px;height:40px;background:linear-gradient(135deg,#a07a5a,#4a3020)}
.t-name{top:888px;font-size:15px;font-weight:300;color:#444}
.t-role{top:908px;font-size:10px;color:#777}
.bubble{top:886px;width:202px;height:87px;background:var(--sky);border-radius:3px;color:#fff;font-size:10px;line-height:18.5px;padding:12px 10px 0 36px}
.bubble::before{content:"";position:absolute;left:-8px;top:18px;border:8px solid transparent;border-left:none;border-right-color:var(--sky)}
.bubble .q{position:absolute;left:14px;top:10px;font-size:22px;font-weight:700;line-height:22px}
.footer{left:0;top:996px;width:1024px;height:162px;background:var(--navy)}
.f-brand{left:120px;top:1024px;display:flex;align-items:center;gap:7px;color:#fff}
.f-brand .mark{width:42px;height:42px;border-radius:50%;border:2px solid #fff}
.f-brand .nm{font-size:15px;line-height:1.05}
.f-brand .nm small{display:block;font-size:9px;text-align:center;letter-spacing:1px}
.f-text{color:#8fb0c8;font-size:10px;line-height:16px}
.f-head{top:1022px;font-size:12px;font-weight:700;color:#fff}
.f-line{left:344px;font-size:10px;color:#fff;line-height:16px}
.f-icon{left:320px}
.email{left:499px;top:1105px;width:131px;height:29px;background:#1d2a33;color:#ccc;font-size:10px;padding:9px 10px}
.subscribe{left:630px;top:1105px;width:70px;height:29px;background:var(--sky);color:#fff;font-size:10px;text-align:center;padding-top:9px}
.social{top:1049px;width:26px;height:26px;border-radius:50%;background:#0a3e63}
.bottom{left:0;top:1158px;width:1024px;height:42px;background:var(--navy-dark)}
.copy{left:121px;top:1171px;font-size:10px;color:#8fb0c8}
.bnav a{position:absolute;top:1171px;font-size:10px;color:#8fb0c8;text-decoration:none}
.bnav a.active{color:#fff}
</style>
</head>
<body>
<div class="abs topbar">
  <div class="abs info" style="left:690px">
    <svg width="22" height="12" viewBox="0 0 22 12"><rect x="7" y="1" width="14" height="10" fill="none" stroke="#8fc7ea" stroke-width="1.2"/><path d="M7 1l7 6 7-6M0 4h5M2 7h4" stroke="#8fc7ea" stroke-width="1.2" fill="none"/></svg>
    info@mlcoach.com
  </div>
  <div class="abs info" style="left:810px">
    <svg width="14" height="14" viewBox="0 0 14 14"><path d="M3 1l2 3-1 1.5c1 2 2.5 3.5 4.5 4.5L10 9l3 2-1.5 2C6 13 1 8 1 2.5z" fill="none" stroke="#8fc7ea" stroke-width="1.2"/></svg>
    +1800.555.0199
  </div>
</div>
<div class="abs header"></div>
<div class="abs brand-box">
  <div class="brand-mark"></div>
  <div class="brand-name">Mara Lindqvist<small>LIFECOACH</small></div>
</div>
<nav class="nav">
  <a class="active" style="left:591px">Home</a>
  <a style="left:658px">Services</a>
  <a style="left:735px">Blog</a>
  <a style="left:794px">About</a>
  <a style="left:861px">Contact</a>
</nav>

<div class="abs hero" role="img" aria-label="Photo of a person standing on a hillside at sunset"></div>
<p class="abs hero-quote">Dont be afraid to stand for what you believe in,<br>even if that means standing alone...</p>
<div class="abs dots"><i></i><i class="on"></i><i></i><i></i></div>

<h1 class="abs welcome" style="font-weight:300;font-size:24px">Welcome to <b>Mara Lindqvist</b> Life Coach</h1>

<div class="abs card-img" style="left:121px;background:linear-gradient(135deg,#c9b8a0,#6c7a52 50%,#e8e8e4)" role="img" aria-label="Photo of three people talking in an office"></div>
<h2 class="abs card-title" style="left:120px;font-weight:400">About Us</h2>
<p class="abs card-text" style="left:120px">Lorem ipsum dolor sit amet, consectetur adipisicing elit, sed do eiusmod tempor incididunt ut labore et dolore magna aliqua.</p>

<div class="abs card-img" style="left:390px;background:linear-gradient(135deg,#8a6a52,#e9ecee 55%,#f2efe9)" role="img" aria-label="Photo of two women smiling in conversation"></div>
<h2 class="abs card-title" style="left:389px;font-weight:700">Services</h2>
<p class="abs card-text" style="left:389px">Lorem ipsum dolor sit amet, consectetur adipisicing elit, sed do eiusmod tempor incididunt ut labore et dolore magna aliqua.</p>

<div class="abs news-head">
  <svg width="16" height="16" viewBox="0 0 16 16"><rect x="1.5" y="3" width="13" height="11.5" fill="none" stroke="#8a97a2" stroke-width="1.4"/><path d="M1.5 6.5h13M5 1v4M11 1v4" stroke="#8a97a2" stroke-width="1.4"/></svg>
  Latest News
</div>
<div class="abs news-rule"></div>

<div class="abs news-title" style="top:607px">There are many variations of passages</div>
<div class="abs news-thumb" style="top:631px" role="img" aria-label="Photo of business people at work"></div>
<p class="abs news-text" style="top:629px">The point of using Lorem Ipsum is that it has a more-or-less normal distribution of letters, as opposed..</p>
<div class="abs news-date" style="top:680px">▦ 8 December 2013</div>

<div class="abs news-title" style="top:707px">All the Lorem Ipsum generators</div>
<div class="abs news-thumb" style="top:731px" role="img" aria-label="Photo of a business meeting"></div>
<p class="abs news-text" style="top:729px">The point of using Lorem Ipsum is that it has a more-or-less normal distribution of letters, as opposed..</p>
<div class="abs news-date" style="top:780px">▦ 8 December 2013</div>

<div class="abs band" role="img" aria-label="Soft sunset sky background"></div>
<h2 class="abs band-title">Client Testimonials</h2>

<div class="abs avatar" style="left:140px" role="img" aria-label="Client portrait"></div>
<div class="abs t-name" style="left:194px">Tom Harwick</div>
<div class="abs t-role" style="left:194px">Businessman</div>
<div class="abs bubble" style="left:298px"><span class="q">“</span>Mauris urnaei elit, mattis non urna acem, ullamcorper vula putatem lorem.</div>

<div class="abs avatar" style="left:544px" role="img" aria-label="Client portrait"></div>
<div class="abs t-name" style="left:598px">Elena Marsh</div>
<div class="abs t-role" style="left:598px">Housewife</div>
<div class="abs bubble" style="left:702px"><span class="q">“</span>Mauris urnaei elit, mattis non urna acem, ullamcorper vula putatem lorem.</div>

<footer class="abs footer"></footer>
<div class="abs f-brand"><div class="mark"></div><div class="nm">Mara Lindqvist<small>LIFECOACH</small></div></div>
<p class="abs f-text" style="left:121px;top:1086px;width:170px">Donec volutpat, mi vel egestas eleif-end, dolor arcu iaculis nunc. Fusce gravida tortor felis, ac dictum risus</p>

<div class="abs f-head" style="left:318px">Contact Details</div>
<svg class="abs f-icon" style="top:1056px" width="14" height="14" viewBox="0 0 14 14"><path d="M3 1l2 3-1 1.5c1 2 2.5 3.5 4.5 4.5L10 9l3 2-1.5 2C6 13 1 8 1 2.5z" fill="#5f8fb2"/></svg>
<div class="abs f-line" style="top:1055px">+1800-555-0142</div>
<svg class="abs f-icon" style="top:1082px" width="13" height="10" viewBox="0 0 13 10"><rect x=".6" y=".6" width="11.8" height="8.8" fill="none" stroke="#5f8fb2" stroke-width="1.2"/><path d="M.6 .6l5.9 5 5.9-5" fill="none" stroke="#5f8fb2" stroke-width="1.2"/></svg>
<div class="abs f-line" style="top:1079px">hello@mlcoach.com</div>
<svg class="abs f-icon" style="left:322px;top:1105px" width="10" height="14" viewBox="0 0 10 14"><path d="M5 0a5 5 0 0 1 5 5c0 3.5-5 9-5 9S0 8.5 0 5a5 5 0 0 1 5-5z" fill="#5f8fb2"/><circle cx="5" cy="5" r="1.8" fill="#0b4f7e"/></svg>
<div class="abs f-line" style="top:1103px">Your Address, Your Country<br>Your Zip Code</div>

<div class="abs f-head" style="left:500px">Newsletter</div>
<p class="abs f-text" style="left:499px;top:1056px;width:200px">Ipsum dolor sit amet, teft consecte tur adipiscing elit ut eunt.</p>
<div class="abs email">Email Address</div>
<div class="abs subscribe">Subscribe</div>

<div class="abs f-head" style="left:726px">Get Social</div>
<div class="abs social" style="left:726px"></div>
<div class="abs social" style="left:765px"></div>
<div class="abs social" style="left:803px"></div>
<div class="abs social" style="left:841px"></div>

<div class="abs bottom"></div>
<div class="abs copy">Copyright © 2014 - MARA LINDQVIST. All Rights reserved</div>
<nav class="bnav">
  <a class="active" style="left:593px">Home</a>
  <a style="left:659px">Services</a>
  <a style="left:737px">Blog</a>
  <a style="left:795px">About</a>
  <a style="left:862px">Contact</a>
</nav>
</body>
</html>
```